Brightmill Data Works

Our company is about IT hardwares and IT solutions. IT hardware such as PC, RAMS, storage and servers. IT solutions such as project management, BA. We are also selling new technology too.

Target Market(s)

Consumer, Small to Medium Business, Corporate

Requirements
Must have
• The business card must have the following:
• Name:
• Title:
• Contact Number:
• Email address:
• Website:
• Color: Must match the logo color upgrade

```html
<!DOCTYPE html>
<html lang="en">
<head>
<meta charset="utf-8">
<title>Brightmill Data Works – Business Card</title>
<link rel="stylesheet" href="https://fonts.googleapis.com/css2?family=Roboto:wght@400;500;700&display=swap">
<style>
  :root {
    --backdrop: #2a2a2a;
    --card-dark: #4a4b4b;
    --card-light: #ffffff;
    --accent: #d9892e;
    --ink-light: #f4f4f4;
    --ink-dark: #47484a;
  }
  * { margin: 0; padding: 0; box-sizing: border-box; }
  html, body { width: 1200px; height: 930px; overflow: hidden; }
  body {
    background: var(--backdrop);
    font-family: "Roboto", Arial, sans-serif;
    position: relative;
  }
  .card {
    position: absolute;
    width: 580px;
    height: 330px;
    border-radius: 16px;
    overflow: hidden;
    box-shadow: 0 14px 30px rgba(0,0,0,.45);
  }
  .card-front { left: 90px; top: 100px; background: var(--card-dark); }
  .card-back  { left: 530px; top: 500px; background: var(--card-dark); }

  .brand {
    position: absolute;
    display: flex;
    align-items: center;
    gap: 14px;
    font-weight: 700;
    text-transform: uppercase;
    letter-spacing: 1px;
  }
  .brand-mark { width: 22px; height: 22px; background: var(--accent); flex: none; }
  .brand-name { font-size: 32px; line-height: 1; }
  .card-front .brand { left: 0; right: 0; top: 140px; justify-content: center; }
  .card-front .brand-name { color: var(--ink-light); }
  .card-back .brand { right: 34px; top: 58px; }
  .card-back .brand-name {
    color: var(--ink-dark);
    font-size: 27px;
    line-height: 1.1;
    width: 210px;
  }

  .back-shape { position: absolute; inset: 0; width: 100%; height: 100%; }

  .contact {
    position: absolute;
    left: 34px;
    bottom: 28px;
    color: var(--ink-light);
    font-size: 14px;
    line-height: 1.4;
  }
  .person-name { color: var(--accent); font-size: 22px; font-weight: 500; text-transform: uppercase; line-height: 1.1; }
  .person-title { font-size: 14px; margin-bottom: 14px; }
  .address { margin-bottom: 12px; }
  .contact-list { list-style: none; }
  .contact-list li { display: flex; align-items: center; gap: 10px; }
  .contact-list svg { width: 12px; height: 12px; flex: none; }
  .site-highlight { color: var(--accent); }
</style>
</head>
<body>

  <section class="card card-front" aria-label="Card front">
    <div class="brand">
      <span class="brand-mark"></span>
      <span class="brand-name">Brightmill Data Works</span>
    </div>
  </section>

  <section class="card card-back" aria-label="Card back">
    <svg class="back-shape" viewBox="0 0 580 330" preserveAspectRatio="none" aria-hidden="true">
      <path d="M200 0 Q290 250 580 232 L580 0 Z" fill="var(--card-light)"/>
      <path d="M200 0 Q290 250 580 232" fill="none" stroke="var(--accent)" stroke-width="6"/>
    </svg>

    <div class="brand">
      <span class="brand-mark"></span>
      <span class="brand-name">Brightmill<br>Data Works</span>
    </div>

    <div class="contact">
      <p class="person-name">Daniel Corwin</p>
      <p class="person-title">Director</p>
      <p class="address">2210 Larkfield Ave<br>Alder, CA 95120-4418</p>
      <ul class="contact-list">
        <li>
          <svg viewBox="0 0 12 12"><path d="M3 1 L5 3.5 L4 5 Q5 7 7 8 L8.5 7 L11 9 L10 11 Q4 11 1 3 Z" fill="var(--accent)"/></svg>
          555-214-7730
        </li>
        <li>
          <svg viewBox="0 0 12 12"><rect x="1" y="2.5" width="10" height="7" fill="none" stroke="var(--accent)" stroke-width="1.2"/><path d="M1 2.5 L6 7 L11 2.5" fill="none" stroke="var(--accent)" stroke-width="1.2"/></svg>
          info@brightmilldata.com
        </li>
        <li>
          <svg viewBox="0 0 12 12"><circle cx="6" cy="6" r="5" fill="none" stroke="var(--accent)" stroke-width="1.2"/><path d="M1 6 H11 M6 1 Q3 6 6 11 M6 1 Q9 6 6 11" fill="none" stroke="var(--accent)" stroke-width="1"/></svg>
          <span>www.<span class="site-highlight">brightmilldata</span>.com</span>
        </li>
      </ul>
    </div>
  </section>

</body>
</html>
```